New business card for a regional office of a US M&A company

We need business card for a finance company, office based in Hong Kong , our Head office is in US, our business is to Merge and acquires companies , the new office will be a regional office for the Asia Pacific region. We want to use the head office logo as attached ( but don't have to be exactly the same, can be a variation to it) as a base and then add Asia Pacific alongside the logo.
We would prefer to have be bilingual Eng + Chinese, although we don't really have Chinese company name .

Industry/Entity Type

Business

Contact Information for Business Card

Clara Jo Tsang
 

VP,
APAC M&A Operations
Orin Vantage Asia Pacific Limited
 
Unit 1407, K18
18 Tai Lok Shan Road, 
Hong Kong 
 
M: +852 6038 1742
T : +852 2836 4100
F : +852 2836 4177
VOIP: 4158
 
cjtsang@orinvantage.com

Font styles to use
Serif
Sans Serif

Colors

Designer to choose colors to be used in the design.

Requirements
Must have
• APAC Office

```html
<!DOCTYPE html>
<html lang="en">
<head>
<meta charset="utf-8">
<title>Orin Vantage Asia Pacific – Business Card</title>
<link href="https://fonts.googleapis.com/css2?family=Ubuntu:wght@500;700&family=Open+Sans:wght@400;600;700&display=swap" rel="stylesheet">
<style>
  :root {
    --stage: #3a3a3c;
    --card-black: #1f1f21;
    --card-dark: #262628;
    --accent: #1ba9d2;
    --accent-deep: #0f7fa3;
    --white: #ffffff;
    --soft-white: #e9e9ea;
    --ink: #16181b;
    --emboss: #3b3b3e;
  }
  * { margin: 0; padding: 0; box-sizing: border-box; }
  html, body {
    width: 799px; height: 1200px; overflow: hidden;
    background: var(--stage);
  }
  .canvas { position: relative; width: 799px; height: 1200px; }

  .card {
    position: absolute; left: 70px;
    width: 660px; height: 377px;
    border-radius: 4px;
    overflow: hidden;
    box-shadow: 0 18px 40px rgba(0,0,0,.45);
  }
  .card--front { top: 150px; background: var(--card-black); }
  .card--back  { top: 680px; background: var(--card-dark); }

  /* Front */
  .front-brand {
    position: absolute; inset: 0;
    display: flex; align-items: center; justify-content: center; gap: 18px;
  }
  .front-brand__mark {
    width: 44px; height: 44px; border: 5px solid var(--emboss);
  }
  .front-brand__name {
    font-family: "Ubuntu", sans-serif; font-weight: 700;
    font-size: 50px; letter-spacing: 2px; color: var(--emboss);
  }

  /* Back */
  .wave { position: absolute; inset: 0; }
  .back-brand {
    position: absolute; left: 34px; top: 92px;
    display: flex; align-items: center; gap: 14px;
  }
  .back-brand__mark { width: 32px; height: 32px; border: 4px solid var(--white); }
  .back-brand__name {
    font-family: "Ubuntu", sans-serif; font-weight: 700;
    font-size: 36px; letter-spacing: 1px; color: var(--accent); line-height: 1;
  }
  .back-brand__web {
    position: absolute; left: 80px; top: 134px;
    font-family: "Open Sans", sans-serif; font-size: 12px;
    letter-spacing: 5px; color: var(--soft-white);
  }

  .contact { position: absolute; left: 34px; top: 170px; font-family: "Open Sans", sans-serif; }
  .contact__company {
    font-weight: 700; font-size: 15px; color: var(--accent); margin-bottom: 8px;
  }
  .contact__list { list-style: none; }
  .contact__item {
    display: flex; align-items: center; gap: 10px;
    font-size: 14px; line-height: 21px; color: var(--white);
  }
  .contact__item svg { width: 12px; height: 12px; flex: none; }
  .contact__label { color: var(--accent); }

  .person {
    position: absolute; right: 40px; top: 108px; text-align: center;
    font-family: "Ubuntu", sans-serif; color: var(--ink);
  }
  .person__name { font-weight: 700; font-size: 21px; margin-bottom: 6px; }
  .person__title {
    font-family: "Open Sans", sans-serif; font-size: 14px; line-height: 18px;
  }

  .address {
    position: absolute; right: 40px; bottom: 30px; text-align: right;
    font-family: "Open Sans", sans-serif; font-size: 14px; line-height: 19px;
    color: var(--white);
  }
</style>
</head>
<body>
<main class="canvas">

  <section class="card card--front" aria-label="Card front">
    <div class="front-brand">
      <span class="front-brand__mark"></span>
      <span class="front-brand__name">ORIN VANTAGE</span>
    </div>
  </section>

  <section class="card card--back" aria-label="Card back">
    <svg class="wave" viewBox="0 0 660 377" preserveAspectRatio="none" aria-hidden="true">
      <path d="M0,0 H660 V262 C560,252 470,205 400,125 C330,45 200,22 0,32 Z" fill="var(--accent)"/>
      <path d="M0,32 C200,22 330,45 400,125 C470,205 560,252 660,262 V270 C555,262 462,214 392,134 C322,56 200,34 0,44 Z" fill="#1a1a1c"/>
      <path d="M0,44 C200,34 322,56 392,134 C462,214 555,262 660,270 V288 C548,282 452,232 382,152 C312,74 200,56 0,62 Z" fill="var(--soft-white)"/>
    </svg>

    <div class="back-brand">
      <span class="back-brand__mark"></span>
      <span class="back-brand__name">ORIN VANTAGE</span>
    </div>
    <div class="back-brand__web">www.orinvantage.com</div>

    <div class="contact">
      <p class="contact__company">Orin Vantage Asia Pacific Limited</p>
      <ul class="contact__list">
        <li class="contact__item">
          <svg viewBox="0 0 12 12"><rect x="3" y="0.5" width="6" height="11" rx="1" fill="var(--accent)"/><rect x="4" y="2" width="4" height="6" fill="var(--card-dark)"/></svg>
          +852 6038 1742
        </li>
        <li class="contact__item">
          <svg viewBox="0 0 12 12"><path d="M2,1 L4.5,1 L5.5,4 L4,5 C5,7 6,8 8,9 L9,7.5 L12,8.5 V11 C6,11 1,6 1,1 Z" fill="var(--accent)"/></svg>
          +852 2836 4100
        </li>
        <li class="contact__item">
          <svg viewBox="0 0 12 12"><rect x="1" y="4" width="10" height="6" rx="1" fill="var(--accent)"/><rect x="3" y="1" width="6" height="4" fill="var(--accent)"/></svg>
          +852 2836 4177, <span class="contact__label">VOIP:</span> 4158
        </li>
        <li class="contact__item">
          <svg viewBox="0 0 12 12"><rect x="0.5" y="2" width="11" height="8" fill="var(--accent)"/><path d="M0.5,2 L6,7 L11.5,2" fill="none" stroke="var(--card-dark)" stroke-width="1"/></svg>
          cjtsang@orinvantage.com
        </li>
      </ul>
    </div>

    <div class="person">
      <p class="person__name">Clara Jo Tsang</p>
      <p class="person__title">Vice President,<br>APAC M&amp;A<br>Operations</p>
    </div>

    <address class="address" style="font-style:normal">
      Unit 1407, K18<br>
      18 Tai Lok Shan<br>
      Road, Hong Kong
    </address>
  </section>

</main>
</body>
</html>
```